Zilata - Sketches from a quiet road

🎨 Design Guidelines
1. Overall Impression

Dignified, spiritual, timeless

Central focus on sand dunes with footsteps as the main motif

Mood: calm, light, spirituality, hope

2. Color Scheme

Background: warm sand tones (beige, golden, brown)

Light source (sun/beam): soft gold/white

Typography: gold or warm yellow, metallic effect preferred (gold foil in print)

Spine and back cover: darker gradient from sand tones to deep blue/black for strong readability

3. Imagery

Front cover: sand dunes with clear footsteps leading towards light/horizon

No figurative depictions of people

Optional: subtle Islamic ornaments or geometric borders as a background accent

4. Typography

Title: “Zīlāta” → large, serif font, elegant, in gold

Subtitle: “Sketches From A Quiet Road” → smaller, clean & modern, also gold/white

Author: Idrīs-Wahīd Salmūn Qāzinī → bottom of the front cover, smaller size

Spine: Title + Arabic word زيلاتة vertically placed, harmonized with the style

5. Back Cover

Short blurb/description (provided by client)

Highlighted keywords in large type: "Courage. Integrity. Faith."

ISBN + barcode at the bottom left

Background: continuation of the sand texture from the front cover (with or without footsteps)

6. Finishing Options (Print)

Gold foil stamping for the title

Matte cover with selective gloss (eg on the light or ornaments)

High-quality, sturdy cover stock

Target Market(s)

Islamic

Font styles to use
Serif

Requirements
Must have
• read the guidelines!
Nice to have
• read the guidelines!
Should not have
• read the guidelines!

```html
<!DOCTYPE html>
<html lang="en">
<head>
<meta charset="utf-8">
<title>Zīlāta — Sketches From A Quiet Road — Cover Spread</title>
<link rel="stylesheet" href="https://fonts.googleapis.com/css2?family=Cormorant+Garamond:ital,wght@0,500;0,600;1,500&family=Open+Sans:wght@400&family=Amiri:wght@400&display=swap">
<style>
  :root {
    --page-bg: #ffffff;
    --navy-deep: #161a26;
    --navy-mid: #1b2a3a;
    --gold-warm: #f3dc8a;
    --white: #ffffff;
    --ink-light: #f2f2f2;
    --spine-olive: #6a5a36;
    --spine-dark: #2c2a26;
    --spine-brown: #a0662f;
    --spine-navy: #1e2a4a;
    --gold: linear-gradient(180deg, #c79a4c 0%, #fff4a8 45%, #e8c978 65%, #a8742c 100%);
  }
  * { margin: 0; padding: 0; box-sizing: border-box; }
  html, body { width: 1200px; height: 872px; overflow: hidden; background: var(--page-bg); }

  .spread {
    position: absolute; left: 43px; top: 43px; width: 1114px; height: 786px;
    box-shadow: 0 6px 22px rgba(0,0,0,.45);
  }

  .gold-text {
    background: var(--gold);
    -webkit-background-clip: text; background-clip: text;
    color: transparent;
  }

  /* Back cover */
  .back-cover {
    position: absolute; left: 0; top: 0; width: 524px; height: 786px;
    background: linear-gradient(180deg, var(--navy-deep) 0%, var(--navy-deep) 38%, var(--navy-mid) 55%, var(--navy-deep) 100%);
    overflow: hidden;
  }
  .back-cover .backdrop { position: absolute; inset: 0; }
  .back-title {
    position: absolute; left: 0; width: 524px; top: 124px; text-align: center;
    font-family: "Cormorant Garamond", serif; font-weight: 500; font-size: 84px; line-height: 1;
  }
  .back-subtitle {
    position: absolute; left: 0; width: 524px; top: 220px; text-align: center;
    font-family: "Cormorant Garamond", serif; font-style: italic; font-weight: 500;
    font-size: 25px; letter-spacing: 3.5px; color: var(--white);
  }
  .keywords {
    position: absolute; left: 0; width: 524px; top: 286px; text-align: center;
    font-family: "Cormorant Garamond", serif; font-weight: 600; font-size: 24px;
    letter-spacing: 3px; color: var(--gold-warm);
  }
  .blurb {
    position: absolute; left: 33px; width: 457px;
    font-family: "Open Sans", sans-serif; font-size: 11.5px; line-height: 16.5px;
    color: var(--ink-light); text-align: justify; letter-spacing: .2px;
    hyphens: auto; -webkit-hyphens: auto;
  }
  .blurb.first { top: 335px; }
  .blurb.second { top: 419px; }
  .blurb.beside-photo { top: 488px; left: 140px; width: 350px; letter-spacing: .1px; }
  .author-photo { position: absolute; left: 33px; top: 490px; width: 96px; height: 92px; background: var(--white); }
  .isbn-box { position: absolute; left: 168px; top: 625px; width: 187px; height: 54px; background: var(--white); }

  /* Spine */
  .spine {
    position: absolute; left: 524px; top: 0; width: 66px; height: 786px;
    background: linear-gradient(180deg, var(--spine-olive) 0%, var(--spine-dark) 16%, var(--spine-dark) 26%, var(--spine-brown) 55%, var(--spine-brown) 62%, var(--spine-navy) 92%);
  }
  .spine-title {
    position: absolute; left: 6px; top: 135px; writing-mode: vertical-rl;
    font-family: "Cormorant Garamond", serif; font-weight: 500; font-size: 54px; line-height: 56px;
  }
  .spine-arabic {
    position: absolute; left: 10px; top: 522px; writing-mode: vertical-rl;
    font-family: "Amiri", serif; font-size: 40px; line-height: 44px;
  }

  /* Front cover */
  .front-cover {
    position: absolute; left: 590px; top: 0; width: 524px; height: 786px; overflow: hidden;
  }
  .front-cover .artwork { position: absolute; inset: 0; }
  .front-title {
    position: absolute; left: 0; width: 524px; top: 40px; text-align: center;
    font-family: "Cormorant Garamond", serif; font-weight: 500; font-size: 150px; line-height: 1;
  }
  .front-subtitle {
    position: absolute; left: 0; width: 524px; top: 208px; text-align: center;
    font-family: "Cormorant Garamond", serif; font-style: italic; font-weight: 500;
    font-size: 32px; letter-spacing: 2.5px; color: var(--white);
  }
  .author {
    position: absolute; left: 0; width: 524px; top: 730px; text-align: center;
    font-family: "Cormorant Garamond", serif; font-weight: 500; font-size: 22px;
    letter-spacing: 1.5px; color: var(--white); text-transform: uppercase;
  }
</style>
</head>
<body>
  <div class="spread">
    <section class="back-cover">
      <svg class="backdrop" width="524" height="786" role="img" aria-label="Faint night-time dunes with a pale moon and footprints in the sand">
        <defs>
          <radialGradient id="moonGlow" cx="0.5" cy="0.5" r="0.5">
            <stop offset="0" stop-color="#2a3a52" stop-opacity=".7"/>
            <stop offset="1" stop-color="#2a3a52" stop-opacity="0"/>
          </radialGradient>
        </defs>
        <circle cx="272" cy="300" r="60" fill="url(#moonGlow)"/>
      </svg>
      <div class="back-title gold-text">Zīlāta</div>
      <div class="back-subtitle">Sketches From A Quiet Road</div>
      <div class="keywords">COURAGE. INTEGRITY. FAITH</div>
      <p class="blurb first">Lorem ipsum dolor sit amet, consectetur adipiscing elit, sed do eiusmod tempor incididunt ut labore et dolore magna aliqua. Quis ipsum suspendisse ultrices gravida. Risus commodo viverra maecenas accumsan lacus vel facilisis. Lorem ipsum dolor sit amet, consectetur adipiscing elit, sed do eiusmod</p>
      <p class="blurb second">Lorem ipsum dolor sit amet, consectetur adipiscing elit, sed do eiusmod tempor incididunt ut labore et dolore magna aliqua. Quis ipsum suspendisse ultrices gravida. Risus commodo viverra maecenas accumsan lacus vel facili-</p>
      <div class="author-photo"></div>
      <p class="blurb beside-photo">Lorem ipsum dolor sit amet, consectetur adipiscing elit, sed do eiusmod tempor incididunt ut labore et dolore magna aliqua. Quis ipsum suspendisse ultrices gravida. Risus commodo viverra maecenas accumsan lacus vel facilisis. Quis ipsum suspendisse ultrices gravida. Risus commodo viverra maecenas accumsan lacus vel facilisis.</p>
      <div class="isbn-box"></div>
    </section>

    <section class="spine">
      <div class="spine-title gold-text">Zīlāta</div>
      <div class="spine-arabic gold-text" lang="ar" dir="rtl">زيلاتة</div>
    </section>

    <section class="front-cover">
      <svg class="artwork" width="524" height="786" role="img" aria-label="Painted desert dunes with footprints leading up a ridge toward a setting sun under a deep rust sky">
        <defs>
          <linearGradient id="frontScene" x1="0" y1="0" x2="0" y2="1">
            <stop offset="0" stop-color="#6a1f00"/>
            <stop offset="0.3" stop-color="#8a3208"/>
            <stop offset="0.4" stop-color="#c4520f"/>
            <stop offset="0.42" stop-color="#9fd6d4"/>
            <stop offset="0.6" stop-color="#b3620c"/>
            <stop offset="1" stop-color="#a8580c"/>
          </linearGradient>
        </defs>
        <rect width="524" height="786" fill="url(#frontScene)"/>
      </svg>
      <div class="front-title gold-text">Zīlāta</div>
      <div class="front-subtitle">Sketches From A Quiet Road</div>
      <div class="author">Idrīs-Wahīd Salmūn Qāzinī</div>
    </section>
  </div>
</body>
</html>
```